Cat-products company needs smart, yet endearing, business card

We need a business card design for a new, but up-and-running, business based in Honolulu, Hawaii. The business is Purrnest Nook Co. Our first product is the most environmentally-friendly cat grass kit ever seen on the planet. Future products, currently in the R&D phase, will include a variety of exciting cat scratchers. We also do consulting work to help apartment-dwellers make their home more cat-friendly and, in the future, plan on doing full, custom installs of structure to create high walkways for cats.

Target Market(s)

Middle-aged, apartment-dwelling, middle-class workers who own 1 or more cats and who dote on them.

Industry/Entity Type

Pet Care

Contact Information for Business Card

A striking, professional, yet warm and friendly design is what we're after.

Font styles to use
Serif
Sans Serif
Other font styles liked:
• Comfortaa

Colors

Designer to choose colors to be used in the design.

Requirements
Must have
• The company logo: (see attachment)
• The company name: Purrnest Nook Co
• The web address: www.purrnestnookco.com
• Email: support@purrnestnookco.com
• Phone: +1 (808) 571 6023
• Update (Fri Jun 30 3017 7:45pm Hawaii Time) I would like, is possible, uploaded picture of the cat grass kit on the back of the card with some text along the lines of: Purrnest Nook Co - Maker Of The Leafiest Feline Sprout Set Yet
Nice to have
• A cat picture, cartoon, real or silhouette that illustrates cats in action and/or relaxing; ie using the apartment space to live, play and relax in and being well-contented.
• Most of the website is done in the font: Comfortaa. It might be nice to continue using this for brand consistency.
Should not have
• Hard-to-read fonts.

```html
<!DOCTYPE html>
<html lang="en">
<head>
<meta charset="utf-8">
<title>Purrnest Nook Co — Business Card</title>
<link href="https://fonts.googleapis.com/css2?family=Open+Sans:wght@400;600;700;800&display=swap" rel="stylesheet">
<style>
  :root {
    --backdrop: #ececec;
    --card-white: #fbfbfb;
    --brand-yellow: #fdb300;
    --brand-brown: #5a3328;
    --ink: #3a3a3a;
    --card-shadow: 0 10px 26px rgba(0,0,0,0.14);
  }
  * { margin: 0; padding: 0; box-sizing: border-box; }
  html, body {
    width: 1200px; height: 900px; overflow: hidden;
    background: var(--backdrop);
    font-family: "Open Sans", Arial, sans-serif;
  }
  .sheet {
    position: relative; width: 1200px; height: 900px;
    display: flex; align-items: center; justify-content: center; gap: 60px;
  }
  .card {
    position: relative; width: 500px; height: 286px;
    box-shadow: var(--card-shadow);
  }
  .card--front { background: var(--card-white); }
  .card--back {
    background: var(--brand-yellow);
    display: flex; align-items: center; justify-content: center;
  }
  .holder { position: absolute; left: 36px; top: 34px; }
  .holder__name {
    color: var(--brand-yellow); font-weight: 600; font-size: 17px;
    letter-spacing: 0.4px; text-transform: uppercase;
  }
  .holder__role { color: var(--ink); font-size: 11px; margin-top: 1px; }
  .contact {
    position: absolute; left: 36px; top: 124px; list-style: none;
    color: var(--ink); font-size: 12px; line-height: 19px;
  }
  .contact__item { display: flex; align-items: center; gap: 8px; }
  .contact__icon { width: 11px; height: 11px; flex: none; }
  .wordmark {
    display: flex; align-items: center; gap: 10px;
    color: var(--brand-brown); font-weight: 800; letter-spacing: 0.2px;
  }
  .wordmark__mark { background: var(--brand-brown); flex: none; }
  .card--front .wordmark {
    position: absolute; right: 32px; bottom: 46px; font-size: 22px;
  }
  .card--front .wordmark__mark { width: 22px; height: 22px; }
  .card--back .wordmark { font-size: 32px; }
  .card--back .wordmark__mark { width: 30px; height: 30px; }
</style>
</head>
<body>
<main class="sheet">
  <section class="card card--front" aria-label="Business card front">
    <div class="holder">
      <p class="holder__name">Marcus Ellery</p>
      <p class="holder__role">Managing Director</p>
    </div>
    <ul class="contact">
      <li class="contact__item">
        <svg class="contact__icon" viewBox="0 0 12 12"><path fill="#fdb300" d="M2.4 0.6l1.9 0.2 0.8 2.6-1.3 1c0.6 1.4 1.6 2.4 2.9 3l1-1.3 2.6 0.8 0.2 1.9C10.4 10.7 9.6 11.4 8.6 11.4 4.4 11 1 7.6 0.6 3.4 0.6 2.4 1.3 1.6 2.4 0.6z"/></svg>
        <span>+1 (808) 571 6023</span>
      </li>
      <li class="contact__item">
        <svg class="contact__icon" viewBox="0 0 12 12"><rect x="0.5" y="2" width="11" height="8" rx="1" fill="#fdb300"/><path d="M1 2.6l5 4 5-4" fill="none" stroke="#fbfbfb" stroke-width="1"/></svg>
        <span>support@purrnestnookco.com</span>
      </li>
      <li class="contact__item">
        <svg class="contact__icon" viewBox="0 0 12 12"><circle cx="6" cy="6" r="5.5" fill="#fdb300"/><path d="M0.8 6h10.4M6 0.6c-2.6 3-2.6 7.8 0 10.8M6 0.6c2.6 3 2.6 7.8 0 10.8" fill="none" stroke="#fbfbfb" stroke-width="0.8"/></svg>
        <span>www.purrnestnookco.com</span>
      </li>
    </ul>
    <div class="wordmark">
      <span class="wordmark__mark" aria-hidden="true"></span>
      <span class="wordmark__name">Purrnest Nook Co</span>
    </div>
  </section>

  <section class="card card--back" aria-label="Business card back">
    <div class="wordmark">
      <span class="wordmark__mark" aria-hidden="true"></span>
      <span class="wordmark__name">Purrnest Nook Co</span>
    </div>
  </section>
</main>
</body>
</html>
```